Website Design Project for Beauty & Wellness Professionals

As background information, I have a website that is focused on Beauty & Wellness Professionals:
- Job Search (www.lumarinovo.com)
- Business Classifieds (negocios.lumarinovo.com)
- Freelancer Classifieds (freelancer.lumarinovo.com)
- Course Reviews (cursos.lumarinovo.com)

All those websites use standard templates.

I need a DESIGN for the HOME PAGE (no coding) of the Website Platform that consolidates the four platforms under the same design.

Website designs that we like:
- quelvox.com
- brintmoor.com

Target Market(s)

Brazilian Professionals from Beauty & Wellness sector

Industry/Entity Type

Business

Requirements
Must have
• Website designs that we like:
- quelvox.com
- brintmoor.com

```html
<!DOCTYPE html>
<html lang="en">
<head>
<meta charset="utf-8">
<title>Lumarinovo – Beauty &amp; Wellness Professionals</title>
<link href="https://fonts.googleapis.com/css2?family=Source+Sans+3:wght@300;400;600&family=Fira+Sans+Condensed:wght@700&family=Open+Sans:ital,wght@0,400;0,700;1,400&display=swap" rel="stylesheet">
<style>
:root{
  --blue:#2a9ccb;
  --blue-dark:#1f86b3;
  --link:#2b7fb8;
  --orange:#e8662f;
  --text:#333;
  --muted:#666;
  --panel-bg:#f3f3f3;
  --line:#dcdcdc;
  --star:#3a9a2a;
  --footer:#333;
  --footer-bottom:#222;
  --social:#5a7d93;
}
*{box-sizing:border-box;margin:0;padding:0}
html,body{width:823px;height:1200px;overflow:hidden}
body{position:relative;background:#fff;font-family:Arial,Helvetica,sans-serif;color:var(--text)}
.abs{position:absolute}

/* header */
.header{left:0;top:0;width:823px;height:89px;background:linear-gradient(#fff,#f2f2f2)}
.brand{left:72px;top:30px;display:flex;align-items:center;gap:6px;font-family:'Source Sans 3',sans-serif;font-size:22px;color:var(--blue)}
.brand .dot{width:12px;height:12px;border-radius:50%;background:var(--blue)}
.contact{top:8px;display:flex;align-items:center;gap:5px;font-size:12px}
.contact svg{width:18px;height:18px}
.phone{left:470px;font-weight:bold;font-size:13px;color:#222}
.email{left:608px;color:var(--link);text-decoration:underline;font-size:11px}
.stay{right:78px;top:35px;font-family:'Open Sans',sans-serif;font-style:italic;font-size:9px;color:#333}
.social{left:473px;top:56px;display:flex;gap:5px}
.social span{width:30px;height:30px;border-radius:50%;background:var(--social)}

/* nav */
.nav{left:0;top:89px;width:823px;height:32px;background:linear-gradient(var(--blue),var(--blue-dark));display:flex;align-items:center;padding-left:72px}
.nav a{font-family:'Source Sans 3',sans-serif;font-size:12.5px;color:#fff;text-decoration:none;padding:0 19px;border-right:1px solid rgba(255,255,255,.35);line-height:18px}
.nav a:last-child{border-right:0}

/* hero */
.hero{left:0;top:121px;width:823px;height:236px;background:linear-gradient(180deg,#6f6a4a 0%,#a88a52 40%,#5b4a2c 75%,#2e2a1c 100%)}
.hero-title{left:0;top:86px;width:823px;text-align:center;font-family:'Fira Sans Condensed',sans-serif;font-size:31px;color:#fff;text-shadow:0 2px 3px rgba(0,0,0,.6)}
.search{left:92px;top:135px;width:616px;height:38px;background:rgba(0,0,0,.55);border-radius:3px}
.search .field{top:3px;height:30px;background:#fff;border:1px solid #ccc;border-radius:3px;font-family:'Source Sans 3',sans-serif;font-size:12px;color:#888;padding:7px 8px}
.search .q{left:4px;width:318px}
.search .cat{left:334px;width:194px}
.search .cat svg{position:absolute;right:8px;top:11px}
.search .btn{left:532px;top:3px;width:78px;height:31px;background:var(--orange);border-radius:3px;color:#fff;font-family:'Source Sans 3',sans-serif;font-size:16px;text-align:center;line-height:31px}
.arrow{top:91px;width:34px;height:34px;border-radius:50%;background:rgba(255,255,255,.35)}
.arrow svg{margin:9px}

/* listings */
.listings{left:0;top:357px;width:823px;height:425px;background:var(--panel-bg)}
.tabs{left:78px;top:16px;display:flex;font-family:'Source Sans 3',sans-serif;font-size:17px;font-weight:300}
.tabs span{padding:4px 25px 4px 25px;color:#222}
.tabs .active{background:#fff;color:var(--link);border:1px solid var(--line);border-bottom:0;border-radius:4px 4px 0 0;padding:4px 25px 6px 25px}
.panel{left:78px;top:44px;width:453px;height:366px;background:#fff;border:1px solid var(--line)}
.item{left:11px;width:431px;border-bottom:1px solid #e5e5e5}
.item .logo{left:2px;top:0;width:52px;height:52px;background:#111;border:1px solid #ccc;display:flex;align-items:center;justify-content:center}
.item .logo.bank{background:#1f3c7a}
.item .logo span{width:16px;height:16px;background:#fff}
.item .name{left:65px;top:-2px;font-size:11px;font-weight:bold;color:var(--link)}
.item .stars{left:65px;top:11px;font-size:13px;color:var(--star);letter-spacing:-1px}
.item .stars i{color:#bbb;font-style:normal}
.item .reviews{left:65px;top:32px;font-size:8.5px;color:var(--muted)}
.item .quote{left:141px;top:-2px;width:295px;font-size:9.5px;font-weight:bold;color:var(--link);line-height:12px}
.item .body{left:143px;top:28px;width:295px;font-size:8.5px;line-height:11px}
.item .more{right:12px;top:58px;font-size:8.5px;font-style:italic}

.promo{left:546px;top:24px;width:207px;height:171px;border:1px solid #ccc;background:linear-gradient(90deg,#e9c9b4 0%,#f6e7dc 45%,#fff 60%)}
.promo .name{right:8px;top:64px;font-family:'Source Sans 3',sans-serif;font-size:20px;color:var(--blue)}
.promo .cap{right:8px;top:97px;width:95px;text-align:right;font-family:'Source Sans 3',sans-serif;font-size:10.5px;line-height:12.5px;color:#333}
.ad{left:547px;top:245px;width:206px;height:163px;background:linear-gradient(160deg,#c8c8c8,#9a9a9a)}

/* professionals */
.pros-title{left:75px;top:798px;font-family:'Source Sans 3',sans-serif;font-size:22px;font-weight:300;color:#222}
.card{top:834px;width:158px;height:158px;border:2px solid #e2e2e2;border-radius:4px;background:#fff}
.card.first{background:#eef6fa}
.card .img{left:4px;top:4px;width:146px;height:83px}
.card h3{position:absolute;left:4px;top:93px;font-size:10px;color:var(--link);letter-spacing:.3px}
.card p{position:absolute;left:5px;top:107px;width:148px;font-size:8px;line-height:11px}
.card p.solo{top:102px}

/* footer */
.footer{left:0;top:1027px;width:823px;height:153px;background:var(--footer)}
.fcol{top:18px}
.fcol h4{font-family:'Source Sans 3',sans-serif;font-weight:300;font-size:15px;color:#ddd;padding-bottom:10px;border-bottom:1px solid #444}
.fnav{list-style:none;margin-top:16px}
.fnav li{font-size:8px;color:#eee;line-height:16px;padding-left:10px;position:relative}
.fnav li:before{content:"";position:absolute;left:0;top:6px;width:3px;height:3px;border-radius:50%;background:var(--blue)}
.ftext{font-size:8px;line-height:13px;color:#eee;margin-top:16px}
.tweet{margin-top:18px;font-size:8px;color:#eee;line-height:11px;position:relative}
.tweet .av{position:absolute;left:0;top:0;width:22px;height:22px;background:#8aa}
.tweet .who{padding-left:25px;height:24px}
.tweet .who b{display:block}
.tweet .who span{color:#aaa}
.tweet .date{position:absolute;right:0;top:0;color:#aaa}
.newsin{margin-top:10px;width:158px;height:22px;background:#ddd;font-size:8px;color:#888;padding:6px 22px;position:relative}
.newsin svg{position:absolute;left:7px;top:7px}
.fbrand{margin-top:18px;margin-left:8px;display:flex;align-items:center;gap:5px;font-family:'Source Sans 3',sans-serif;font-size:17px;color:#bbb}
.fbrand span{width:10px;height:10px;border-radius:50%;background:#bbb}
.bottom{left:0;top:1180px;width:823px;height:20px;background:var(--footer-bottom);color:#ddd;font-size:8px;text-align:center;line-height:20px}
</style>
</head>
<body>

<header class="header abs">
  <div class="brand abs"><span class="dot"></span>Lumarinovo</div>
  <div class="contact phone abs">
    <svg viewBox="0 0 18 18"><circle cx="9" cy="9" r="8" fill="#3d8fd1"/><path d="M6 5l2 2-1 1 3 3 1-1 2 2-1.5 1.5C8 13 5 10 4.5 6.5z" fill="#fff"/></svg>
    (555)-014-(2290)
  </div>
  <div class="contact email abs">
    <svg viewBox="0 0 18 18"><circle cx="9" cy="9" r="8" fill="#3d8fd1"/><rect x="4.5" y="6" width="9" height="6" fill="#fff"/><path d="M4.5 6l4.5 3.5L13.5 6" stroke="#3d8fd1" fill="none"/></svg>
    info@lumarinovo.com
  </div>
  <div class="stay abs">Stay Connected:</div>
  <div class="social abs" aria-label="Social links">
    <span></span><span></span><span></span><span></span><span></span><span></span><span></span><span></span>
  </div>
</header>

<nav class="nav abs">
  <a href="#">Home</a><a href="#">Categories of Business</a><a href="#">For Professionals</a><a href="#">For Business</a><a href="#">About Us</a><a href="#">Contact Us</a>
</nav>

<section class="hero abs" role="img" aria-label="Photo of a fishing boat moored on a calm lake at sunset">
  <div class="arrow abs" style="left:10px"><svg width="16" height="16" viewBox="0 0 16 16"><path d="M11 2L5 8l6 6" stroke="#fff" stroke-width="3" fill="none"/></svg></div>
  <div class="arrow abs" style="left:780px"><svg width="16" height="16" viewBox="0 0 16 16"><path d="M5 2l6 6-6 6" stroke="#fff" stroke-width="3" fill="none"/></svg></div>
  <h1 class="hero-title abs">Welcome to the presentation of Lumarinovo</h1>
  <div class="search abs">
    <div class="field q abs">what are you looking for?</div>
    <div class="field cat abs">All Categories<svg width="12" height="8" viewBox="0 0 12 8"><path d="M0 0h12L6 8z" fill="#333"/></svg></div>
    <div class="btn abs">Search</div>
  </div>
</section>

<section class="listings abs">
  <div class="tabs abs"><span class="active">Recents</span><span>Most Viewed</span><span>Random</span></div>
  <div class="panel abs">
    <div class="item abs" style="top:25px;height:75px">
      <div class="logo abs"><span></span></div>
      <div class="name abs">Tellvane</div>
      <div class="stars abs">★★★<i>★★</i></div>
      <div class="reviews abs">1,429 reviews</div>
      <div class="quote abs">“ simply dummy text of the printing and typesetting industry. Lorem Ipsum has been the industry's ”</div>
      <div class="body abs">simply dummy text of the printing and typesetting industry. Lorem Ipsum has been the industry's</div>
      <div class="more abs">read more...</div>
    </div>
    <div class="item abs" style="top:110px;height:77px">
      <div class="logo bank abs"><span></span></div>
      <div class="name abs">Harbor Trust</div>
      <div class="stars abs">★★★<i>★★</i></div>
      <div class="reviews abs">820 reviews</div>
      <div class="quote abs">“ simply dummy text of the printing and typesetting industry. Lorem Ipsum has been the industry's ”</div>
      <div class="body abs">simply dummy text of the printing and typesetting industry. Lorem Ipsum has been the industry's</div>
      <div class="more abs">read more...</div>
    </div>
    <div class="item abs" style="top:193px;height:84px">
      <div class="logo abs"><span></span></div>
      <div class="name abs">Tellvane</div>
      <div class="stars abs">★★★<i>★★</i></div>
      <div class="reviews abs">1,429 reviews</div>
      <div class="quote abs">“ simply dummy text of the printing and typesetting industry. Lorem Ipsum has been the industry's ”</div>
      <div class="body abs">simply dummy text of the printing and typesetting industry. Lorem Ipsum has been the industry's</div>
      <div class="more abs">read more...</div>
    </div>
    <div class="item abs" style="top:284px;height:70px;border-bottom:0">
      <div class="logo bank abs"><span></span></div>
      <div class="name abs">Harbor Trust</div>
      <div class="stars abs">★★★<i>★★</i></div>
      <div class="reviews abs">820 reviews</div>
      <div class="quote abs">“ simply dummy text of the printing and typesetting industry. Lorem Ipsum has been the industry's ”</div>
      <div class="body abs">simply dummy text of the printing and typesetting industry. Lorem Ipsum has been the industry's</div>
      <div class="more abs">read more...</div>
    </div>
  </div>

  <div class="promo abs" role="img" aria-label="Promotional photo of a woman holding a white orchid">
    <div class="name abs">Lumarinovo</div>
    <div class="cap abs">when an unknown printer took a galley of type and scram-bled it to make a type specimen book.</div>
  </div>
  <div class="ad abs" role="img" aria-label="Advertisement for pricing table templates shown on a laptop and phone"></div>
</section>

<h2 class="pros-title abs">Beauty &amp; Wellness Professionals</h2>
<div class="card first abs" style="left:73px">
  <div class="img abs" role="img" aria-label="Photo of a woman searching for jobs on a laptop" style="background:linear-gradient(135deg,#d9c9a8,#8a8270)"></div>
  <h3>Job Search</h3>
  <p>simply dummy text of the printing and typesetting industry. Lorem Ipsum has been the industry's</p>
</div>
<div class="card abs" style="left:247px">
  <div class="img abs" role="img" aria-label="Photo of business people in a meeting" style="background:linear-gradient(135deg,#7a7e86,#2d3138)"></div>
  <h3>Business Classifieds</h3>
  <p>simply dummy text of the printing and typesetting industry. Lorem Ipsum has been the industry's</p>
</div>
<div class="card abs" style="left:420px">
  <div class="img abs" role="img" aria-label="Photo of a makeup artist at work" style="background:linear-gradient(135deg,#c7b8a8,#2a2422)"></div>
  <h3>Freelancer Classifieds</h3>
  <p>simply dummy text of the printing and typesetting industry. Lorem Ipsum has been the industry's</p>
</div>
<div class="card abs" style="left:594px">
  <div class="img abs" role="img" aria-label="Photo of a facial spa treatment" style="background:linear-gradient(135deg,#e9b9b4,#f3e4df)"></div>
  <p class="solo">simply dummy text of the printing and typesetting industry. Lorem Ipsum has been the industry's</p>
</div>

<footer class="footer abs">
  <div class="fcol abs" style="left:80px;width:92px">
    <h4>Navigation</h4>
    <ul class="fnav"><li>About Us</li><li>Best sellers</li><li>News</li><li>Collections</li></ul>
  </div>
  <div class="fcol abs" style="left:197px;width:225px">
    <h4>Latest tweets</h4>
    <div class="tweet">
      <div class="av"></div>
      <div class="date">11 Jul</div>
      <div class="who"><b>Brightmoss</b><span>@TheBrightmoss</span></div>
      We are in the final stages of building our latest product - Orlena for Pagecraft. It's going to use the amazing Shopcraft plugin.
    </div>
  </div>
  <div class="fcol abs" style="left:447px;width:160px">
    <h4>Newsletter</h4>
    <p class="ftext">Vestibulum at lacus id turpis malesuada varius. Donec ultricies mauris vel nisi porta dictum.</p>
    <div class="newsin"><svg width="9" height="7" viewBox="0 0 9 7"><rect width="9" height="7" fill="#555"/><path d="M0 0l4.5 4L9 0" stroke="#ddd" fill="none"/></svg>e-mail address</div>
  </div>
  <div class="fcol abs" style="left:628px;width:125px">
    <h4>About us</h4>
    <p class="ftext">Orlena is a modern responsive HTML5 theme</p>
    <div class="fbrand"><span></span>Lumarinovo</div>
  </div>
</footer>
<div class="bottom abs">Except where noted, copyright © 2010-2012 Lumarinovo</div>

</body>
</html>
```